Professional and creative business card design for recruiting service providers

Our company supports German medium-sized companies in filling vacancies promptly. For this we use social media marketing and bring our customers into the visibility.

We want a professional but also creative design for our business cards.

Please look at lindqvar-staff.de to get an impression of our CI.

Target Market(s)

Small and medium-sized companies in Germany from the industry

Industry/Entity Type

Industrie, Handwerk

Contact Information for Business Card

Name, Position, Telefonnummer, Email, Website

Colors
EE7325
F08F49
F5BC92
FAE3D3
FDF4ED

Requirements
Must have
• A picture of the employee and in the style of www.lindqvar-staff.de

```html
<!DOCTYPE html>
<html lang="de">
<head>
<meta charset="utf-8">
<title>Lindqvar &amp; Staff – Visitenkarte</title>
<link href="https://fonts.googleapis.com/css2?family=Poppins:wght@400;600;700&display=swap" rel="stylesheet">
<style>
  :root {
    --backdrop: #a9a9a9;
    --ink: #000000;
    --brand-orange: #f0602d;
    --paper: #ffffff;
    --photo-light: #dedbd9;
    --photo-dark: #25262c;
  }
  * { box-sizing: border-box; margin: 0; padding: 0; }
  html, body { width: 1200px; height: 1200px; overflow: hidden; }
  body {
    position: relative;
    background: var(--backdrop);
    font-family: "Poppins", sans-serif;
    color: var(--paper);
  }
  .card {
    position: absolute;
    top: 303px;
    height: 594px;
    overflow: hidden;
  }
  .card--front { left: 201px; width: 369px; }
  .card--back { left: 599px; width: 365px; background: var(--brand-orange); }

  .card__header {
    position: absolute; left: 0; top: 0; width: 100%;
    background: var(--ink);
  }
  .card--front .card__header { height: 260px; }
  .card--back .card__header { height: 272px; }

  .brand {
    position: absolute; left: 50px; top: 106px;
    display: flex; align-items: center; gap: 18px;
  }
  .brand__square {
    width: 70px; height: 70px;
    background: var(--brand-orange);
  }
  .brand__name {
    font-weight: 600;
    font-size: 28px;
    line-height: 31px;
    letter-spacing: 1.6px;
    color: var(--paper);
    text-transform: uppercase;
  }

  .employee-photo {
    position: absolute; left: 0; top: 260px; width: 100%; height: 334px;
    background: linear-gradient(180deg, var(--photo-light) 0%, #b9b4b2 45%, var(--photo-dark) 100%);
  }

  .contact {
    position: absolute; left: 0; top: 362px; width: 100%;
    text-align: center;
  }
  .contact__name {
    font-weight: 700; font-size: 29px; line-height: 34px; letter-spacing: 0.3px;
    text-transform: uppercase;
  }
  .contact__role {
    font-weight: 400; font-size: 17px; line-height: 20px; letter-spacing: 0.4px;
  }
  .contact__icons {
    display: flex; align-items: center; justify-content: center; gap: 5px;
    margin-top: 17px;
  }
  .contact__rule { width: 56px; height: 1px; background: var(--paper); opacity: 0.85; }
  .contact__rule:first-child { margin-right: 3px; }
  .contact__rule:last-child { margin-left: 3px; }
  .icon-box {
    width: 28px; height: 28px; border-radius: 3px;
    background: var(--paper);
    display: flex; align-items: center; justify-content: center;
  }
  .icon-box svg { width: 18px; height: 18px; }
  .contact__lines {
    list-style: none; margin-top: 7px;
    font-size: 18px; line-height: 23px; letter-spacing: 0.5px;
  }
</style>
</head>
<body>
  <section class="card card--front">
    <header class="card__header">
      <div class="brand">
        <span class="brand__square"></span>
        <span class="brand__name">Lindqvar<br>&amp; Staff</span>
      </div>
    </header>
    <div class="employee-photo" role="img" aria-label="Portrait photo of the employee seated in an office chair"></div>
  </section>

  <section class="card card--back">
    <header class="card__header">
      <div class="brand">
        <span class="brand__square"></span>
        <span class="brand__name">Lindqvar<br>&amp; Staff</span>
      </div>
    </header>
    <div class="contact">
      <h1 class="contact__name">Jonas Berger</h1>
      <p class="contact__role">Managing Director</p>
      <div class="contact__icons">
        <span class="contact__rule"></span>
        <span class="icon-box" aria-label="Telefon">
          <svg viewBox="0 0 24 24" fill="var(--brand-orange)"><path d="M6.6 10.8a15.5 15.5 0 0 0 6.6 6.6l2.2-2.2c.3-.3.7-.4 1-.2 1.1.4 2.3.6 3.6.6.6 0 1 .4 1 1V20c0 .6-.4 1-1 1C10.6 21 3 13.4 3 4c0-.6.4-1 1-1h3.5c.6 0 1 .4 1 1 0 1.3.2 2.5.6 3.6.1.3 0 .7-.2 1z"/></svg>
        </span>
        <span class="icon-box" aria-label="E-Mail">
          <svg viewBox="0 0 24 24" fill="none" stroke="var(--brand-orange)" stroke-width="2"><rect x="3" y="5" width="18" height="14"/><path d="M3 5l9 8 9-8M3 19l7-7M21 19l-7-7"/></svg>
        </span>
        <span class="icon-box" aria-label="Website">
          <svg viewBox="0 0 24 24" fill="none" stroke="var(--brand-orange)" stroke-width="2"><circle cx="12" cy="12" r="9"/><path d="M3 12h18M12 3c3 3 3 15 0 18M12 3c-3 3-3 15 0 18"/></svg>
        </span>
        <span class="contact__rule"></span>
      </div>
      <ul class="contact__lines">
        <li>030-555 018 274</li>
        <li>info@lindqvar-staff.de</li>
        <li>www.lindqvar-staff.de</li>
      </ul>
    </div>
  </section>
</body>
</html>
```